Jewelers Website

This is for the DESIGN ONLY.
I am a software programmer and will be doing the development.
New website design for
www.lunacrestgems.com.au
Need a fresh new look for an online only jewellery business who produce their jewellery by hand. I would like it designed in a parallax style. Feel free to recommend fonts to use for the site. This is an Australian based company located in NSW so shots of sites in NSW might make nice background images.
http://vornaplex.me/demo/#theme=parallax
To contain the below sections
About Us
Contact Us
Gallery
Testimonials
Diamond Types
The colour scheme is to be Black / White and Silver.
With the Parallax style there will be moving sections and images for added impact.
Target Market(s)
Young Adults mainly engagement jewellery

```html
<!DOCTYPE html>
<html lang="en">
<head>
<meta charset="utf-8">
<title>Lunacrest Gems</title>
<link href="https://fonts.googleapis.com/css2?family=Lato:wght@300;400;700&family=Cormorant+Garamond:wght@500&display=swap" rel="stylesheet">
<style>
:root{
  --ink:#0b0b0b;
  --white:#ffffff;
  --text:#5a5a5a;
  --muted:#7a7a7a;
  --soft:#bdbdbd;
  --panel:#f9f9f9;
  --rule:#d8d8d8;
  --btn:#e2e2e2;
  --btn-small:#f3f3f3;
  --icon-bg:#f0f0f0;
  --icon-mark:#c4c4c4;
}
*{margin:0;padding:0;box-sizing:border-box}
html,body{width:1200px;height:1064px;overflow:hidden;background:var(--white)}
body{position:relative;font-family:'Lato',sans-serif}
.hero{position:absolute;left:0;top:0;width:1200px;height:521px;
  background:radial-gradient(ellipse at 55% 55%,#8a8a8a 0%,#4a4a4a 35%,#1e1e1e 70%,#0d0d0d 100%)}
.logo{position:absolute;left:100px;top:66px;width:163px;height:69px;background:#232323;
  border:1px solid #3a3a3a;display:flex;flex-direction:column;justify-content:center;align-items:center;
  font-family:'Cormorant Garamond',serif;font-weight:500;color:var(--white);font-size:28px;line-height:26px;letter-spacing:.5px}
.nav{position:absolute;top:66px;left:409px;display:flex;list-style:none}
.nav li{color:var(--white);font-weight:700;font-size:14px;line-height:18px}
.nav li+li{margin-left:43px}
.dots{position:absolute;top:462px;left:555px;display:flex;gap:6px}
.dot{width:26px;height:26px;border-radius:50%;background:var(--white)}
.dot.active{background:var(--ink);border:4px solid var(--white)}
.welcome{position:absolute;left:97px;top:511px;width:1007px;height:206px;
  background:linear-gradient(#fdfdfd,#f4f4f4);box-shadow:0 10px 14px -8px rgba(0,0,0,.18);text-align:center}
.welcome h1{position:absolute;left:28px;right:26px;top:34px;font-size:30px;font-weight:700;color:var(--ink);line-height:36px}
.welcome h1::before,.welcome h1::after{content:"";position:absolute;top:22px;height:1px;background:var(--rule);width:222px}
.welcome h1::before{left:0}.welcome h1::after{right:0}
.welcome p{position:absolute;left:60px;right:60px;top:84px;font-size:15px;line-height:19px;color:var(--text)}
.btn{position:absolute;left:439px;top:153px;width:128px;height:39px;background:var(--btn);color:var(--muted);
  font-size:16px;font-weight:300;line-height:39px}
.feature{position:absolute;top:754px;width:260px;text-align:center}
.feature .icon{width:96px;height:96px;border-radius:50%;margin:0 auto;display:block}
.feature h2{margin-top:19px;font-size:18px;font-weight:700;color:var(--ink);line-height:20px}
.feature p{margin-top:6px;font-family:Arial,sans-serif;font-size:13px;line-height:16.5px;color:var(--muted)}
.feature .more{display:block;width:91px;height:27px;margin:10px auto 0;background:var(--btn-small);
  color:var(--soft);font-size:11px;line-height:27px;font-weight:300}
</style>
</head>
<body>
<header class="hero" role="img" aria-label="Close-up photograph of loose brilliant-cut diamonds on dark textured fabric">
  <div class="logo"><span>LUNACREST</span><span>GEMS</span></div>
  <ul class="nav">
    <li>HOME</li><li>ABOUT US</li><li>GALLERY</li><li>TESTIMONIALS</li><li>DIAMOND TYPES</li><li>CONTACT US</li>
  </ul>
  <div class="dots"><span class="dot"></span><span class="dot active"></span><span class="dot"></span></div>
</header>

<section class="welcome">
  <h1>WELCOME TO LUNACREST GEMS</h1>
  <p>Lorem ipsum dolor sit amet, consectetur adipisicing elit, sed do eiusmod tempor incididunt ut labore et dolore magna aliqua. Ut enim ad minim veniam, quis nostrud exercitation ullamco laboris nisi ut aliquip ex ea commodo consequat. Duis aute irure dolor in reprehenderit in voluptate velit esse</p>
  <span class="btn">Read More</span>
</section>

<section class="feature" style="left:93px">
  <svg class="icon" viewBox="0 0 96 96"><circle cx="48" cy="48" r="48" fill="#000"/><circle cx="48" cy="48" r="22" fill="#fff"/><circle cx="49" cy="37" r="3.5" fill="#000"/><path d="M44 44h8v16h3v3H42v-3h3z" fill="#000"/></svg>
  <h2>ABOUT US</h2>
  <p>Lorem ipsum dolor sit amet, consectetur adipisicing elit, sed do eiusmod tempor incididunt ut labore et</p>
  <span class="more">Read More</span>
</section>

<section class="feature" style="left:470px">
  <svg class="icon" viewBox="0 0 96 96"><circle cx="48" cy="48" r="48" fill="#f1f1f1"/>
    <g fill="#c4c4c4"><circle cx="38" cy="54" r="10"/><circle cx="58" cy="36" r="7"/></g>
    <g stroke="#c4c4c4" stroke-width="5"><path d="M38 40v28M24 54h28M28 44l20 20M48 44L28 64"/><path d="M58 27v18M49 36h18M52 30l12 12M64 30L52 42" stroke-width="4"/></g>
    <circle cx="38" cy="54" r="4" fill="#f1f1f1"/><circle cx="58" cy="36" r="3" fill="#f1f1f1"/></svg>
  <h2>OUR SERVICES</h2>
  <p>Lorem ipsum dolor sit amet, consectetur adipisicing elit, sed do eiusmod tempor incididunt ut labore et</p>
  <span class="more">Read More</span>
</section>

<section class="feature" style="left:832px">
  <svg class="icon" viewBox="0 0 96 96"><circle cx="48" cy="48" r="48" fill="#f1f1f1"/>
    <rect x="12" y="36" width="30" height="28" rx="4" fill="#c4c4c4" transform="rotate(-6 27 50)"/>
    <path d="M16 40l12 11 12-12" stroke="#f1f1f1" stroke-width="2.5" fill="none" transform="rotate(-6 27 50)"/>
    <rect x="52" y="36" width="30" height="30" rx="5" fill="#c4c4c4" transform="rotate(8 67 51)"/></svg>
  <h2>CONNECT WITH US</h2>
  <p>Lorem ipsum dolor sit amet, consectetur adipisicing elit, sed do eiusmod tempor incididunt ut labore et</p>
  <span class="more">Read More</span>
</section>
</body>
</html>
```